Cedar & Dawn Unity Fellowship (Tri-Fold Letter Size Brochure

I work at Lantern Bridge Outreach Organization. We currently have a special project for making a design of tri-fold letter size brochure in Chinese version. The purpose for brochure is to mobile Chinese Christian Church to care for world mission by establishing the prayer fellowship over the world. And this brochure will be presented to the conference as promo. I hope this can be done by this weekend. Since this is Chinese, I apologized that we don't have it in English version yet. So you can follow the paragraph as Title, then contents. Please do let me know if any questions. Thanks

I currently update with some photos and text. Please take a look.

In addition, I just simply made a "Draft" for outside & inside for your reference. Of course I am not professional like you are. Hopefully, this will not limit you creation and imagination. Thanks all.

Target Market(s)

Christian Church

Requirements
Must have
• I need a PSD file when job is done, so that I can edit with text.
Nice to have
• We like to have special design (not photos I sent) on the cover side & background such as prayer hands, earth, people connected to touch the world...etc., which can catch people's eye for inspiration, and to connect each other by praying each other.

```html
<!DOCTYPE html>
<html lang="zh">
<head>
<meta charset="utf-8">
<title>Cedar &amp; Dawn Unity Fellowship — Tri-Fold Brochure</title>
<link href="https://fonts.googleapis.com/css2?family=Anton&family=Noto+Sans+SC:wght@400;700&family=Noto+Serif+SC:wght@700&family=Open+Sans:wght@400;700&display=swap" rel="stylesheet">
<style>
  :root{
    --paper:#d9d9d9;
    --navy:#1f2f6b;
    --blue:#2a44a8;
    --red:#c8243a;
    --pink:#f3a9a4;
    --pink-deep:#e8837f;
    --pink-light:#fbe3dc;
    --cream:#f7efe6;
    --yellow:#ffe53b;
    --ink:#5a2a2a;
    --label:#ffffff;
    --photo-warm:#b58a74;
    --earth:#5a7aa6;
    --dove:#e3e7f0;
    --skin:#e7b9a6;
  }
  *{box-sizing:border-box;margin:0;padding:0}
  html,body{width:769px;height:1200px;overflow:hidden;background:var(--paper)}
  body{position:relative;font-family:"Noto Sans SC","Open Sans",sans-serif}
  .sheet-label{position:absolute;font:700 13px "Open Sans",sans-serif;color:var(--label);letter-spacing:.5px;text-shadow:0 1px 1px rgba(0,0,0,.35)}
  .spread{position:absolute;left:56px;width:668px;overflow:hidden;box-shadow:0 2px 6px rgba(0,0,0,.3)}
  .spread--outside{top:56px;height:538px;background:var(--cream)}
  .spread--inside{top:622px;height:518px;background:var(--pink-light)}
  .panel{position:absolute;top:0;height:100%;overflow:hidden}
  .swoosh{position:absolute;left:0;bottom:0;width:100%;height:90px}
  .art{position:absolute}

  /* outside */
  .photo-hero{left:0;top:0;width:443px;height:300px;background:linear-gradient(135deg,#e7ddd5 0%,var(--photo-warm) 50%,#e4d3c4 100%)}
  .art-earth{left:20px;top:230px;width:150px;height:150px;background:var(--earth)}
  .panel--back{left:225px;width:218px}
  .back-body{position:absolute;left:0;top:300px;width:100%;height:238px;background:linear-gradient(180deg,var(--pink-light),var(--pink))}
  .cn-red{font-family:"Noto Serif SC",serif;font-weight:700;color:var(--red);text-align:center;line-height:1.35}
  .cn-blue{font-family:"Noto Serif SC",serif;font-weight:700;color:var(--blue);text-align:center;line-height:1.35}
  .back-title{position:absolute;top:18px;left:0;width:100%;font-size:12px}
  .org-name{font:700 13px "Open Sans",sans-serif;color:var(--ink);text-align:center;line-height:1.2}
  .back-org{position:absolute;top:80px;left:20px;width:178px}
  .back-org .dot{display:block;width:14px;height:14px;border-radius:50%;background:var(--ink);margin:0 auto 6px}
  .small-text{font-size:7px;color:#6a3a3a;text-align:center;line-height:1.4}
  .back-small{position:absolute;top:140px;left:14px;width:190px}
  .flap-note{position:absolute;left:12px;top:12px;width:200px;text-align:left;color:#fff}

  .panel--front{left:443px;width:225px;background:linear-gradient(180deg,#f7c7bd 0%,var(--pink) 55%,var(--pink-deep) 100%)}
  .art-front-globe{left:40px;top:10px;width:145px;height:130px;background:linear-gradient(180deg,#f5c84a,#e89b3a)}
  .front-headline{position:absolute;left:0;top:30px;width:225px;text-align:center;font:400 30px/1 "Anton",sans-serif;color:var(--yellow);-webkit-text-stroke:1.5px var(--navy);letter-spacing:.5px}
  .art-hands{left:40px;top:148px;width:145px;height:92px;background:var(--skin)}
  .front-title{position:absolute;top:246px;left:8px;width:209px;font-size:12px}
  .hearts{position:absolute;left:30px;top:298px;width:34px;height:30px}
  .front-org{position:absolute;top:330px;left:20px;width:185px}
  .front-org .dot{display:block;width:16px;height:16px;border-radius:50%;background:var(--red);margin:0 auto 6px}
  .front-org .org-name{color:var(--red);font-size:15px}
  .front-date{position:absolute;top:420px;left:0;width:100%;text-align:center;font:700 14px "Open Sans",sans-serif;color:var(--blue)}
  .front-sub{position:absolute;top:448px;left:8px;width:209px;font-size:11px}

  /* inside */
  .panel--in{width:223px}
  .panel--in-left{left:0}
  .panel--in-center{left:223px}
  .panel--in-right{left:446px;width:222px}
  .photo-frame{position:absolute;left:14px;top:14px;width:195px;height:140px;border:4px solid var(--red);border-radius:90px 90px 14px 14px;overflow:hidden;background:#fff}
  .photo-frame .art{inset:0}
  .photo-group{background:linear-gradient(160deg,#d9c2a8,#a86a58)}
  .photo-circle{background:linear-gradient(160deg,#c7b7a4,#8a766a)}
  .photo-care{background:linear-gradient(160deg,#e8d8c8,#a89080)}
  .in-title{position:absolute;left:8px;width:207px;font-size:11px}
  .body-text{position:absolute;left:16px;width:191px;font-size:7px;line-height:1.55;color:#5c3434;text-align:justify}
  .in-org{position:absolute;top:292px;left:10px;width:203px;font:700 11px/1.3 "Open Sans",sans-serif;color:var(--blue);text-align:center}
  .art-dove{left:81px;top:334px;width:60px;height:44px;background:var(--dove)}
  .center-org{position:absolute;top:392px;left:16px;width:191px}
  .center-org .dot{display:block;width:14px;height:14px;border-radius:50%;background:var(--red);margin:0 auto 4px}
  .center-org .org-name{color:var(--red);font-size:12px}
  .contact{position:absolute;bottom:8px;font:400 10px "Open Sans",sans-serif;color:#fff}
  .contact--phone{left:14px;font-size:11px}
  .contact--phone b{font-size:13px}
  .contact--mail{right:12px;font-size:7px}
</style>
</head>
<body>
  <span class="sheet-label" style="left:26px;top:30px">OUTSIDE FLAP</span>
  <span class="sheet-label" style="left:366px;top:30px">BACK</span>
  <span class="sheet-label" style="left:600px;top:30px">FRONT</span>

  <section class="spread spread--outside">
    <div class="art photo-hero" role="img" aria-label="Photo of a child embracing a globe with a dove and a cross"></div>
    <div class="art art-earth" role="img" aria-label="Illustration of the earth with a white dove above it"></div>
    <p class="small-text flap-note">同心祷告 关怀世界 宣教使命<br>连结众教会 彼此代祷</p>

    <div class="panel panel--back">
      <div class="back-body">
        <p class="cn-red back-title">山好友富力 板古安眞力<br>平好心好友 安视奥</p>
        <div class="back-org">
          <span class="dot"></span>
          <p class="org-name">Cedar &amp; Dawn Unity Fellowship</p>
        </div>
        <p class="small-text back-small">世界宣教祷告团契 · 联系我们<br>欢迎各地教会加入代祷行列</p>
      </div>
    </div>

    <div class="panel panel--front">
      <div class="art art-front-globe" role="img" aria-label="Illustration of a glowing globe"></div>
      <h1 class="front-headline">LOREM<br>IPSUM<br>TEXT</h1>
      <div class="art art-hands" role="img" aria-label="Illustration of praying hands holding the world"></div>
      <p class="cn-blue front-title">山好友富力 板古安眞力 平好心好友<br>安视奥 祷古安眞力</p>
      <svg class="hearts" viewBox="0 0 34 30" aria-hidden="true">
        <path fill="#d4202f" d="M10 22C3 16 1 12 4 8s8-2 6 2c2-4 7-6 9-2s-2 8-9 14z"/>
        <path fill="#e84a58" d="M24 14c-4-3-5-6-3-8s5-1 4 1c1-2 4-3 5-1s-1 5-6 8z"/>
      </svg>
      <div class="front-org">
        <span class="dot"></span>
        <p class="org-name">Cedar &amp; Dawn Unity Fellowship</p>
      </div>
      <p class="front-date">July 13, 2014</p>
      <p class="cn-blue front-sub">山好友富力 板古安眞力<br>平好心好友 安视奥</p>
    </div>

    <svg class="swoosh" viewBox="0 0 668 90" preserveAspectRatio="none" aria-hidden="true">
      <path fill="#c8243a" d="M0 60 C150 20 300 70 443 40 L443 90 L0 90z" opacity=".9"/>
      <path fill="#1f2f6b" d="M0 72 C160 40 300 85 443 60 L443 90 L0 90z"/>
      <path fill="#1f2f6b" d="M443 55 C520 80 600 40 668 50 L668 90 L443 90z"/>
      <path fill="#ffffff" d="M443 50 C520 74 600 34 668 44 L668 48 C600 40 520 80 443 55z"/>
    </svg>
  </section>

  <section class="spread spread--inside">
    <div class="panel panel--in panel--in-left">
      <div class="photo-frame"><div class="art photo-group" role="img" aria-label="Photo of a church congregation gathered together"></div></div>
      <p class="cn-red in-title" style="top:166px">山好友富力 板古安眞力<br>平好心好友 安视奥</p>
      <p class="body-text" style="top:205px">我们相信祷告能连结世界各地的教会。每一位弟兄姊妹都可以在所在之处为宣教士与福音工场代祷。</p>
      <p class="cn-red in-title" style="top:268px">山好友富力 板古安眞力<br>平好心好友 安视奥</p>
      <p class="body-text" style="top:306px">成立祷告团契，定期聚会，分享宣教消息，彼此扶持，一同关怀世界的需要。欢迎您的教会一起加入。</p>
    </div>

    <div class="panel panel--in panel--in-center">
      <div class="photo-frame"><div class="art photo-circle" role="img" aria-label="Photo of a small group praying in a circle"></div></div>
      <p class="cn-red in-title" style="top:166px">山好友富力 板古安眞力<br>平好心好友 安视奥</p>
      <p class="body-text" style="top:205px">团契聚会以敬拜、代祷与分享为中心，让更多华人教会看见宣教的呼召，同心合意，持续为列国祷告。</p>
      <p class="in-org">Lantern Bridge Outreach<br>Organization</p>
      <div class="art art-dove" role="img" aria-label="Illustration of a flying white dove"></div>
      <div class="center-org">
        <span class="dot"></span>
        <p class="org-name">Cedar &amp; Dawn Unity Fellowship</p>
      </div>
    </div>

    <div class="panel panel--in panel--in-right">
      <div class="photo-frame"><div class="art photo-care" role="img" aria-label="Photo of members caring for an elderly person"></div></div>
      <p class="cn-red in-title" style="top:166px">山好友富力 板古安眞力<br>平好心好友 安视奥</p>
      <p class="body-text" style="top:205px">透过探访与关怀，把基督的爱带到需要的人当中，让祷告化为实际的行动与陪伴。</p>
      <p class="cn-red in-title" style="top:268px">山好友富力 板古安眞力<br>平好心好友 安视奥</p>
      <p class="body-text" style="top:306px">期待与您同工，在各地建立祷告网络，一同见证神在列国中的作为。</p>
    </div>

    <svg class="swoosh" viewBox="0 0 668 90" preserveAspectRatio="none" aria-hidden="true">
      <path fill="#c8243a" d="M0 40 C200 70 450 20 668 45 L668 90 L0 90z"/>
      <path fill="#1f2f6b" d="M0 52 C200 80 450 32 668 56 L668 90 L0 90z"/>
    </svg>
    <p class="contact contact--phone">Call us: <b>010.555.0142</b></p>
    <p class="contact contact--mail">email us: hello@lanternbridge.org</p>
  </section>

  <span class="sheet-label" style="left:70px;top:1150px">Inside Left</span>
  <span class="sheet-label" style="left:335px;top:1150px">Inside Center</span>
  <span class="sheet-label" style="left:565px;top:1150px">Inside Right</span>
</body>
</html>
```